Home Security Company Business Card

Looking for a eye catching business card that is non traditional and stands out but yet still looks professional. It should include all the pertinent information such as name, title, address, telephone, e-mail, website address should definitely stand out and then finally the logo.

Target Market(s)

Residential and Commercial accounts mostly upscale accounts

Industry/Entity Type

Security

Contact Information for Business Card

Name
Title
Address
Office #
Cell #
E-mail
Website

Font styles to use
Serif
Sans Serif

Requirements
Must have
• Logo, two sided color configuration
Nice to have
• You decide
Should not have
• There really aren't any.

```html
<!DOCTYPE html>
<html lang="en">
<head>
<meta charset="utf-8">
<title>Ironhall Protection Group – Business Card</title>
<link href="https://fonts.googleapis.com/css2?family=Open+Sans:wght@400;600;700&display=swap" rel="stylesheet">
<style>
  :root {
    --page-bg: #e9e6e1;
    --card-black: #0b0b0b;
    --card-black-soft: #1a1a1a;
    --brand-red: #7e1518;
    --brand-red-text: #a3211f;
    --brand-gold: #e9a93b;
    --text-light: #f2f2f2;
  }
  * { box-sizing: border-box; margin: 0; padding: 0; }
  html, body {
    width: 1200px;
    height: 900px;
    overflow: hidden;
    background: var(--page-bg);
    font-family: "Open Sans", Arial, sans-serif;
  }
  .canvas {
    position: relative;
    width: 1200px;
    height: 900px;
  }
  .card {
    position: absolute;
    left: 300px;
    width: 600px;
    height: 343px;
    border-radius: 4px;
    overflow: hidden;
    background: radial-gradient(ellipse at 40% 40%, var(--card-black-soft), var(--card-black) 70%);
    box-shadow: 0 10px 28px rgba(0,0,0,0.25);
  }
  .card--front { top: 90px; }
  .card--back { top: 467px; }

  .brand {
    display: flex;
    align-items: center;
    gap: 12px;
    color: var(--brand-red-text);
    font-weight: 600;
    letter-spacing: 0.04em;
    text-transform: uppercase;
  }
  .brand__dot {
    border-radius: 50%;
    background: var(--brand-red-text);
    flex: none;
  }
  .card--front .brand {
    position: absolute;
    left: 50%;
    top: 50%;
    transform: translate(-50%, -50%);
    font-size: 22px;
    white-space: nowrap;
  }
  .card--front .brand__dot { width: 40px; height: 40px; }

  .card--back .brand {
    position: absolute;
    right: 34px;
    top: 56px;
    font-size: 14px;
    white-space: nowrap;
  }
  .card--back .brand__dot { width: 26px; height: 26px; }

  .wave {
    position: absolute;
    inset: 0;
    width: 600px;
    height: 343px;
  }

  .contact {
    position: absolute;
    left: 46px;
    top: 50px;
    color: var(--text-light);
  }
  .contact__name {
    color: var(--brand-gold);
    font-weight: 700;
    font-size: 19px;
    line-height: 1.2;
  }
  .contact__title {
    font-size: 14px;
    line-height: 1.3;
    margin-bottom: 18px;
  }
  .contact__address {
    font-size: 15px;
    line-height: 1.35;
    font-style: normal;
    margin-bottom: 16px;
  }
  .contact__list { list-style: none; }
  .contact__item {
    display: flex;
    align-items: center;
    gap: 9px;
    font-size: 15px;
    line-height: 1.45;
  }
  .contact__icon {
    width: 12px;
    height: 12px;
    flex: none;
    fill: var(--brand-gold);
  }
</style>
</head>
<body>
<main class="canvas">

  <section class="card card--front" aria-label="Card front">
    <div class="brand">
      <span class="brand__dot"></span>
      <span class="brand__name">Ironhall Protection Group</span>
    </div>
  </section>

  <section class="card card--back" aria-label="Card back">
    <svg class="wave" viewBox="0 0 600 343" aria-hidden="true">
      <path d="M0,300 C200,292 330,280 410,240 C480,205 540,175 600,160 L600,343 L0,343 Z" fill="var(--brand-gold)"/>
      <path d="M0,312 C200,304 340,292 420,250 C490,214 545,186 600,172 L600,343 L0,343 Z" fill="#000"/>
      <path d="M0,318 C200,310 345,298 425,256 C495,220 548,193 600,180 L600,343 L0,343 Z" fill="var(--brand-red)"/>
    </svg>

    <div class="brand">
      <span class="brand__dot"></span>
      <span class="brand__name">Ironhall Protection Group</span>
    </div>

    <div class="contact">
      <p class="contact__name">Daniel Carter</p>
      <p class="contact__title">Managing Director</p>
      <address class="contact__address">48 Harbor Lane, Suite 210<br>Westbridge, WB 40218.</address>
      <ul class="contact__list">
        <li class="contact__item">
          <svg class="contact__icon" viewBox="0 0 12 12" aria-hidden="true"><path d="M1,4 Q6,0 11,4 L10,6 L8,5 L8,4 Q6,3 4,4 L4,5 L2,6 Z M2,7 L10,7 L11,11 L1,11 Z"/></svg>
          <span>044-872 310 554</span>
        </li>
        <li class="contact__item">
          <svg class="contact__icon" viewBox="0 0 12 12" aria-hidden="true"><path d="M3,0 H9 V12 H3 Z M4,1.5 V9 H8 V1.5 Z"/></svg>
          <span>044-872 310 667</span>
        </li>
        <li class="contact__item">
          <svg class="contact__icon" viewBox="0 0 12 12" aria-hidden="true"><path d="M0,2 H12 V10 H0 Z M1,3 L6,7 L11,3 Z" fill-rule="evenodd"/></svg>
          <span>info@ironhallprotect.com</span>
        </li>
        <li class="contact__item">
          <svg class="contact__icon" viewBox="0 0 12 12" aria-hidden="true"><path d="M1,8 L4,5 L5.5,6.5 L3,9 L3.5,9.5 L6,7 L7,8 L4,11 Z M11,4 L8,7 L6.5,5.5 L9,3 L8.5,2.5 L6,5 L5,4 L8,1 Z"/></svg>
          <span>www.ironhallprotect.com</span>
        </li>
      </ul>
    </div>
  </section>

</main>
</body>
</html>
```